Website for new dental office

I am Dr. Colin Ashford and am building a new dental practice. I specialize in general dentistry. I am young and have a higher end dental practice incorporating very new technologies and would like my website to reflect that. As many dental patients are older, the website must be very easy to navigate. I would like patients to be able to request appointments, and will eventually add on patient information forms (the health history, etc, that you normally fill out in the practice) from my practice management software, so leave an area for that.

Industry/Entity Type

Building

```html
<!DOCTYPE html>
<html lang="en">
<head>
<meta charset="utf-8">
<title>Ashford Dental Clinic</title>
<link href="https://fonts.googleapis.com/css2?family=Open+Sans:ital,wght@0,300;0,400;0,600;1,400&display=swap" rel="stylesheet">
<style>
:root{
  --slate:#688a9f;
  --slate-dark:#56778d;
  --slate-deep:#4d6d82;
  --ink:#5a7a8f;
  --text:#555b60;
  --black:#1f2326;
  --soft:#eef1f3;
  --line:#d8dee2;
  --white:#ffffff;
}
*{box-sizing:border-box;margin:0;padding:0}
html,body{width:971px;height:1200px;overflow:hidden;background:var(--white)}
body{position:relative;font-family:"Open Sans",Arial,sans-serif;color:var(--text)}
.abs{position:absolute}

/* header */
.brand{left:140px;top:10px;display:flex;align-items:center;gap:8px;white-space:nowrap}
.brand-mark{width:34px;height:34px;border-radius:50%;background:var(--slate);flex:none}
.brand-name{font-size:16px;color:var(--slate);line-height:1.15}
.brand-tag{font-size:9px;color:var(--text);font-family:Arial,sans-serif}
.follow{right:138px;top:18px;display:flex;align-items:center;gap:7px;font-size:10px;color:var(--ink)}
.follow .dot{width:23px;height:23px;border-radius:50%;background:var(--slate)}

/* nav */
.navband{left:0;top:58px;width:971px;height:60px;background:var(--slate)}
.doctor{left:139px;top:68px;color:var(--white)}
.doctor b{display:block;font-weight:400;font-size:18px}
.doctor i{font-size:10px}
.nav{left:342px;top:58px;display:flex;height:60px}
.nav a{color:var(--white);text-decoration:none;font-size:12px;display:flex;align-items:center;padding:0 17px}
.nav a.active{background:var(--slate-dark);padding:0 21px}

/* hero */
.hero-photo{left:139px;top:138px;width:479px;height:292px;background:linear-gradient(120deg,#cfcfcf,#9c9c9c 55%,#e2e2e2)}
.caption{left:139px;top:323px;width:215px;height:84px;background:rgba(104,138,159,.85);color:var(--white);padding:9px 19px;white-space:nowrap;overflow:hidden}
.caption h2{font-weight:300;font-size:18px;line-height:1.25}
.caption .up{font-size:10.5px;font-weight:600;margin-top:4px;line-height:1.4}
.caption .sm{font-size:10.5px;line-height:1.5}
.slide-nav{left:564px;top:400px;width:38px;height:18px;background:var(--slate-dark)}
.booking{left:618px;top:138px;width:215px;height:292px;background:var(--slate);color:var(--white)}
.booking h3{position:absolute;left:24px;top:20px;font-weight:400;font-size:24px;line-height:1.3}
.booking .sub{position:absolute;left:24px;top:83px;font-size:15px;font-weight:300}
.field{position:absolute;border:1px solid #e4ecf0;height:24px;font-size:10px;padding:4px 9px;color:#eef3f6}
.submit{position:absolute;left:24px;top:242px;width:172px;height:32px;background:var(--slate-deep);font-family:Arial,sans-serif;font-weight:700;font-size:10px;display:flex;align-items:center;justify-content:center;gap:5px}

/* welcome */
.welcome{left:0;width:971px;text-align:center}
.welcome h1{font-weight:300;font-size:25px;color:var(--ink)}
.lead{top:497px;font-family:Arial,sans-serif;font-size:11.5px;color:var(--black)}
.intro{top:522px;font-family:Arial,sans-serif;font-size:9.5px;line-height:20px;color:var(--text)}
.btn{border:1px solid var(--ink);color:var(--ink);font-family:Arial,sans-serif;font-weight:700;display:flex;align-items:center;justify-content:center;gap:4px}
.more{left:384px;top:575px;width:203px;height:38px;font-size:10px}

/* columns */
.col{top:650px;width:213px}
.col h2{font-weight:300;font-size:19px;color:var(--ink);margin-left:-2px}
.col .photo{margin-top:12px;height:116px}
.col p{margin-top:13px;font-family:Arial,sans-serif;font-size:8.3px;line-height:16px}
.col .btn{margin-top:13px;width:92px;height:29px;font-size:9px}

/* testimonials */
.clients{left:0;top:938px;width:971px;height:184px;background:var(--soft);border-top:1px solid var(--line)}
.clients h2{position:absolute;width:100%;top:20px;text-align:center;font-weight:300;font-size:19px;color:var(--ink)}
.arrows{position:absolute;left:812px;top:30px}
.avatar{position:absolute;top:72px;width:77px;height:77px;border-radius:50%}
.quote{position:absolute;top:84px;width:220px;font-family:Arial,sans-serif}
.quote b{display:block;font-weight:400;font-size:10px;color:var(--ink)}
.quote .meta{font-size:7.5px;font-style:italic;color:var(--ink);margin:3px 0 5px}
.quote p{font-size:8.3px;line-height:16px}
.divider{position:absolute;left:482px;top:80px;width:1px;height:62px;background:var(--line)}

/* footer */
.footer{left:0;top:1122px;width:971px;height:78px;background:var(--slate);color:var(--white)}
.footer .brand{top:22px;left:140px}
.footer .brand-name{font-size:15px}
.footer .brand-mark{background:var(--white)}
.footer .brand-name,.footer .brand-tag{color:var(--white)}
.footer .sep{position:absolute;left:342px;top:23px;width:1px;height:37px;background:var(--white)}
.fnav{position:absolute;left:369px;top:23px;display:flex;gap:35px;font-size:9px}
.copy{position:absolute;left:369px;top:45px;font-size:9px}
</style>
</head>
<body>

<header>
  <div class="abs brand">
    <span class="brand-mark"></span>
    <div><div class="brand-name">Ashford Dental Clinic</div><div class="brand-tag">specialised in general dentistry</div></div>
  </div>
  <div class="abs follow">Follow us :
    <span class="dot" aria-label="Social network 1"></span><span class="dot" aria-label="Social network 2"></span><span class="dot" aria-label="Social network 3"></span><span class="dot" aria-label="Social network 4"></span><span class="dot" aria-label="Social network 5"></span>
  </div>
</header>

<div class="abs navband"></div>
<div class="abs doctor"><b>Dr. Colin Ashford</b><i>is specialised in general dentistry</i></div>
<nav class="abs nav">
  <a class="active">Home</a><a>About us</a><a>Services</a><a>specialised</a><a>Appointment</a><a>Conatct us</a>
</nav>

<section>
  <div class="abs hero-photo" role="img" aria-label="Black and white photo of a dentist treating a smiling patient"></div>
  <div class="abs caption">
    <h2>Ashford Dental Clinic</h2>
    <div class="up">DR. COLIN ASHFORD IS</div>
    <div class="sm">specialised in general dentistry</div>
  </div>
  <svg class="abs slide-nav" viewBox="0 0 38 18"><path d="M12 5l-4 4 4 4M26 5l4 4-4 4" fill="none" stroke="#fff" stroke-width="1.3"/><path d="M19 5v8" stroke="#fff" stroke-width=".8"/></svg>
  <div class="abs booking">
    <h3>Ashford<br>Dental Clinic</h3>
    <div class="sub">Request Appointment</div>
    <div class="field" style="left:24px;top:116px;width:172px">Name :</div>
    <div class="field" style="left:24px;top:148px;width:172px">Email :</div>
    <div class="field" style="left:24px;top:178px;width:172px">Phone :</div>
    <div class="field" style="left:24px;top:210px;width:81px">Date :</div>
    <div class="field" style="left:114px;top:210px;width:82px">Time :</div>
    <div class="submit">SUBMIT NOW <svg width="10" height="8" viewBox="0 0 10 8"><path d="M1 1l3 3-3 3M5 1l3 3-3 3" fill="none" stroke="#fff" stroke-width="1.3"/></svg></div>
  </div>
</section>

<section>
  <div class="abs welcome" style="top:452px"><h1>Welcome to Ashford Dental Clinic</h1></div>
  <div class="abs welcome lead">He provides higher end dental practice incorporating very new technologies.</div>
  <div class="abs welcome intro">It is a long established fact that a reader will be distracted by the readable content of a page when looking at its layout. The point of using<br>Lorem Ipsum is that it has a more-or-less normal distribution of letters, as opposed to using 'Content here...</div>
  <div class="abs btn more">CLICK HERE FOR MORE INFO <svg width="11" height="9" viewBox="0 0 11 9"><path d="M1 1l3.5 3.5L1 8M5.5 1L9 4.5 5.5 8" fill="none" stroke="currentColor" stroke-width="1.3"/></svg></div>
</section>

<section>
  <div class="abs col" style="left:139px">
    <h2>Dr. Colin Ashford</h2>
    <div class="photo" role="img" aria-label="Portrait of the dentist in a white coat" style="background:linear-gradient(90deg,#f4f4f4,#d9d6d2 50%,#f1f1f1)"></div>
    <p>It is a long established fact that a reader will be distracted by the readable content of a page when looking It is a long established fact that a reader...</p>
    <div class="btn">CLICK HERE <svg width="9" height="8" viewBox="0 0 9 8"><path d="M1 1l3 3-3 3M5 1l3 3-3 3" fill="none" stroke="currentColor" stroke-width="1.2"/></svg></div>
  </div>
  <div class="abs col" style="left:379px">
    <h2>General Dentistry</h2>
    <div class="photo" role="img" aria-label="Dentist examining a patient in the chair" style="background:linear-gradient(120deg,#bfd3de,#d8c2b4 45%,#9db6c6)"></div>
    <p>It is a long established fact that a reader will be distracted by the readable content of a page when looking It is a long established fact that a reader...</p>
    <div class="btn">CLICK HERE <svg width="9" height="8" viewBox="0 0 9 8"><path d="M1 1l3 3-3 3M5 1l3 3-3 3" fill="none" stroke="currentColor" stroke-width="1.2"/></svg></div>
  </div>
  <div class="abs col" style="left:620px">
    <h2>Specialised</h2>
    <div class="photo" role="img" aria-label="Dentist in green scrubs with a smiling patient" style="background:linear-gradient(120deg,#2f8f8c,#5aaaa4 50%,#d9c0ad)"></div>
    <p>It is a long established fact that a reader will be distracted by the readable content of a page when looking It is a long established fact that a reader...</p>
    <div class="btn">CLICK HERE <svg width="9" height="8" viewBox="0 0 9 8"><path d="M1 1l3 3-3 3M5 1l3 3-3 3" fill="none" stroke="currentColor" stroke-width="1.2"/></svg></div>
  </div>
</section>

<section class="abs clients">
  <h2>Happy Clients</h2>
  <svg class="arrows" width="16" height="10" viewBox="0 0 16 10"><path d="M5 2L2 5l3 3M11 2l3 3-3 3" fill="none" stroke="#5a7a8f" stroke-width="1.2"/></svg>
  <div class="avatar" role="img" aria-label="Photo of a smiling couple" style="left:139px;background:radial-gradient(circle,#d7b49a,#6b4a3a)"></div>
  <div class="quote" style="left:234px">
    <b>Marcus Hale</b>
    <div class="meta">Journalist &nbsp;&nbsp;| &nbsp;&nbsp;Posted on 25 mar 2014</div>
    <p>It is a long established fact that a reader will be distracted by the readable content of a page when looking...</p>
  </div>
  <div class="divider"></div>
  <div class="avatar" role="img" aria-label="Photo of a smiling woman" style="left:512px;background:radial-gradient(circle,#f0d5c4,#7a5440)"></div>
  <div class="quote" style="left:607px">
    <b>Marcus Hale</b>
    <div class="meta">Journalist &nbsp;&nbsp;| &nbsp;&nbsp;Posted on 25 mar 2014</div>
    <p>It is a long established fact that a reader will be distracted by the readable content of a page when looking...</p>
  </div>
</section>

<footer class="abs footer">
  <div class="abs brand">
    <span class="brand-mark"></span>
    <div><div class="brand-name">Ashford Dental Clinic</div><div class="brand-tag">specialised in general dentistry</div></div>
  </div>
  <div class="sep"></div>
  <div class="fnav"><span>Home</span><span>About us</span><span>Services</span><span>Appointment</span><span>Conatct us</span></div>
  <div class="copy">Copyright © 2014. Ashford Dental Clinic. All Rights Reserved</div>
</footer>

</body>
</html>
```